Professional Photography Business cards

I need business cards that include my logo which I have uploaded. I run a photography business. I am open to ideas but I would like one side to have my logo and the other side to have my contact info. I don't have a website made but I do own a website domain. I have uploaded 2 different logo color schemes. My business colors are Blue, black , and white.

Business Name
Business Phone Number
Business Email
Business Website address
Instagram

Industry/Entity Type

Professional Photography

Contact Information for Business Card

Phone Number: 916-384-7702 email: info@tlane-studio.example Instagram: @t.lanestudio website doman- www.tlane-studio.example

Requirements
Must have
• I like the idea of a business card with a full black background front and back of card. My colors must include royal blue, black, and white

```html
<!DOCTYPE html>
<html lang="en">
<head>
<meta charset="UTF-8">
<title>T. Lane Studio – Business Cards</title>
<link rel="stylesheet" href="https://fonts.googleapis.com/css2?family=Roboto:wght@400&display=swap">
<style>
  :root {
    --stage: #2a2a2a;
    --stage-edge: #141414;
    --card-white: #ffffff;
    --card-black: #121212;
    --royal-blue: #1a1aa8;
    --ink-black: #0b0b0b;
    --text-white: #f4f4f4;
  }
  * { margin: 0; padding: 0; box-sizing: border-box; }
  html, body { width: 1200px; height: 900px; overflow: hidden; }
  body {
    position: relative;
    background: radial-gradient(ellipse at 50% 45%, var(--stage) 0%, var(--stage-edge) 100%);
    font-family: "Roboto", Arial, sans-serif;
  }
  .card {
    position: absolute;
    width: 620px;
    height: 354px;
    box-shadow: 0 12px 30px rgba(0,0,0,0.55);
  }
  .card--front { left: 150px; top: 90px; background: var(--card-white); }
  .card--back  { left: 430px; top: 456px; background: var(--card-black); }

  .brand {
    position: absolute;
    display: flex;
    align-items: center;
    gap: 14px;
  }
  .brand__name {
    font-size: 40px;
    font-weight: 400;
    color: var(--royal-blue);
    letter-spacing: 0.5px;
  }
  .brand__dot {
    width: 46px; height: 46px;
    border-radius: 50%;
    border: 5px solid var(--ink-black);
  }
  .card--front .brand { left: 170px; top: 150px; }
  .card--back .brand { left: 250px; top: 60px; }
  .card--back .brand__dot { border-color: var(--text-white); }

  .contact {
    position: absolute;
    left: 56px;
    top: 190px;
    list-style: none;
    color: var(--text-white);
    font-size: 19px;
  }
  .contact__item {
    display: flex;
    align-items: center;
    gap: 12px;
    height: 28px;
  }
  .contact__item--social { margin-top: 18px; }
  .contact__icon { width: 18px; height: 18px; flex: none; }
  .contact__square {
    width: 20px; height: 20px;
    border: 2px solid var(--royal-blue);
    border-radius: 5px;
    flex: none;
  }
</style>
</head>
<body>
  <section class="card card--front">
    <div class="brand">
      <span class="brand__name">T. Lane Studio</span>
      <span class="brand__dot"></span>
    </div>
  </section>

  <section class="card card--back">
    <div class="brand">
      <span class="brand__name">T. Lane Studio</span>
      <span class="brand__dot"></span>
    </div>

    <ul class="contact">
      <li class="contact__item">
        <svg class="contact__icon" viewBox="0 0 24 24" aria-hidden="true">
          <path d="M6.6 10.8a15 15 0 0 0 6.6 6.6l2.2-2.2a1 1 0 0 1 1-.25 11.4 11.4 0 0 0 3.6.57 1 1 0 0 1 1 1V20a1 1 0 0 1-1 1A17 17 0 0 1 3 4a1 1 0 0 1 1-1h3.5a1 1 0 0 1 1 1c0 1.25.2 2.45.57 3.57a1 1 0 0 1-.25 1z" fill="var(--royal-blue)"/>
        </svg>
        <span>916-384-7702</span>
      </li>
      <li class="contact__item">
        <svg class="contact__icon" viewBox="0 0 24 24" aria-hidden="true">
          <rect x="2" y="5" width="20" height="14" rx="2" fill="var(--royal-blue)"/>
          <path d="M3 6l9 7 9-7" fill="none" stroke="var(--card-black)" stroke-width="1.6"/>
        </svg>
        <span>info@tlane-studio.example</span>
      </li>
      <li class="contact__item">
        <svg class="contact__icon" viewBox="0 0 24 24" aria-hidden="true">
          <g fill="none" stroke="var(--royal-blue)" stroke-width="1.8">
            <circle cx="12" cy="12" r="9"/>
            <ellipse cx="12" cy="12" rx="4" ry="9"/>
            <path d="M3 12h18"/>
          </g>
        </svg>
        <span>www.tlane-studio.example</span>
      </li>
      <li class="contact__item contact__item--social">
        <span class="contact__square"></span>
        <span>@t.lanestudio</span>
      </li>
    </ul>
  </section>
</body>
</html>
```